Wedding Videography Wordpress Website Theme

We need a modern and high-end website look for our wedding video and film business. We film weddings all over the United Kingdom and at European destinations so need something to reflect our work. The website should be visually stunning with images and videos being the focal point as this is what our services are.

The current website is www.brunolessway.com so you will be able to see our brand.

My Instagram is www.instagram.com/brunolesswayfilms so a new design should link in with this idea.

We need the following pages designed by the winning designer

1 - Homepage
2 - Films Index Page
3 - Testimonials
4 - Prices
5 - Reviews
6 - Meet Bruno (About)
7 - Contact
8 - Blog Index
9 - Blog Page

All pages must be consistent so have a similar style.

Pages on menu:
Meet Bruno
Videos
Packages
Testimionials
Journal (Blog)
Contact

We require a responsive look too. Over 90% of our visitors access the website via their mobile devices.

```html
<!DOCTYPE html>
<html lang="en">
<head>
<meta charset="utf-8">
<title>Blog Page – Bruno Lessway Wedding Films</title>
<link href="https://fonts.googleapis.com/css2?family=Cormorant+Garamond:wght@500;600&family=Jost:wght@400;500&display=swap" rel="stylesheet">
<style>
:root{
  --canvas:#f0f0f2;
  --paper:#ffffff;
  --gold:#a8883f;
  --gold-btn:#dccb98;
  --band:#e4d6ad;
  --ink:#2b2b2b;
  --muted:#6b6b6b;
  --rule:#e2e2e2;
}
*{margin:0;padding:0;box-sizing:border-box}
html,body{width:1200px;height:2809px;overflow:hidden}
body{background:var(--canvas);position:relative;font-family:'Jost',sans-serif;color:var(--ink)}
.abs{position:absolute}
.serif{font-family:'Cormorant Garamond',serif}
.page-label{left:104px;top:44px;width:87px;height:343px;background:linear-gradient(180deg,#3a3a3a 0%,#1c1c1c 100%);opacity:.85;border-radius:40px}
.desktop{left:256px;top:0;width:714px;height:2809px;background:var(--paper)}
.mobile{left:1021px;top:0;width:150px;height:2809px;background:var(--paper)}
.photo{background:radial-gradient(ellipse at 60% 40%,#b49a82 0%,#7a6a58 35%,#3f3a33 100%)}
.photo.warm{background:radial-gradient(ellipse at 70% 45%,#d6c7b4 0%,#8a6d4d 35%,#2f3a58 75%,#3a2e22 100%)}
.photo.green{background:linear-gradient(180deg,#b5a9b0 0%,#8e8a88 25%,#6f7a5a 50%,#596a3c 75%,#4c5a38 100%)}
.photo.blue{background:radial-gradient(ellipse at 45% 60%,#e8e4dc 0%,#9cc0d8 30%,#4f7fa5 60%,#3f4a5a 100%)}
.photo.field{background:radial-gradient(ellipse at 65% 45%,#f2efe8 0%,#c49a48 18%,#8a6a30 50%,#4b3717 100%)}
.photo.suit{background:radial-gradient(ellipse at 55% 45%,#e0cdb5 0%,#5a5448 40%,#1f1f22 100%)}
.hero-shade{background:radial-gradient(ellipse at 30% 40%,#a89784 0%,#6e6558 35%,transparent 60%),radial-gradient(ellipse at 75% 35%,#9a8a76 0%,#5a5448 40%,transparent 65%),linear-gradient(180deg,#6b6a62,#3a352e)}
.brand{font-family:'Jost',sans-serif;font-weight:500;color:#fff;letter-spacing:.22em;font-size:11px;white-space:nowrap}
.nav a{position:absolute;font-size:7.5px;color:#fff;text-decoration:none;letter-spacing:.04em;font-weight:500;white-space:nowrap}
.btn{display:flex;align-items:center;justify-content:center;background:var(--gold-btn);font-size:7px;font-weight:500;letter-spacing:.04em;color:var(--ink);position:absolute}
.btn.white{background:#fff;font-weight:400;font-size:8px;letter-spacing:0}
.hero-title{color:#fff;text-align:center;letter-spacing:.06em;font-weight:500}
.hero-sub{color:#fff;text-align:center;font-size:9.5px}
.h-gold{color:var(--gold);text-align:center;letter-spacing:.04em;font-family:'Cormorant Garamond',serif;font-weight:600}
.small{font-size:7px;line-height:15.5px;color:var(--muted)}
.center{text-align:center}
.arrow{background:var(--gold-btn);display:flex;align-items:center;justify-content:center}
.arrow.light{background:#fff}
.band{background:var(--band)}
.card{background:#fff;display:flex;align-items:center}
.card .lbl{font-size:6.5px;color:var(--muted)}
.card .val{font-size:10px;color:var(--ink)}
.ico{border:1.2px solid var(--gold);border-radius:3px}
.sup-ico{border-radius:50%;background:radial-gradient(circle at 50% 45%,#f3ead2 0%,#e2cd98 55%,#c9ab63 100%)}
.datebox{background:var(--gold);color:#fff;text-align:center;font-family:'Cormorant Garamond',serif}
.post-title{font-family:'Cormorant Garamond',serif;font-weight:600;font-size:12px;color:var(--ink)}
.read{font-size:6.5px;color:var(--gold)}
.read::after{content:"";display:inline-block;width:16px;height:1px;background:var(--gold);margin-left:6px;vertical-align:middle}
.foot-h{font-size:9.5px;color:var(--ink)}
.foot-h::after{content:"";display:inline-block;width:14px;height:1px;background:var(--ink);margin-left:6px;vertical-align:middle}
.foot-t{font-size:7.5px;color:var(--ink)}
</style>
</head>
<body>

<div class="abs page-label" role="img" aria-label="Hand-lettered page title: Blog Index"></div>

<!-- ================= DESKTOP ================= -->
<section class="abs desktop">
  <div class="abs hero-shade" style="left:0;top:0;width:714px;height:367px" role="img" aria-label="Bride and groom laughing under falling confetti"></div>
  <div class="abs brand" style="left:72px;top:46px">BRUNO LESSWAY</div>
  <nav class="nav">
    <a style="left:236px;top:48px">MEET BRUNO</a>
    <a style="left:304px;top:48px">VIDEOS</a>
    <a style="left:356px;top:48px">PACKAGES</a>
    <a style="left:423px;top:48px">TESTIMONIALS</a>
    <a style="left:499px;top:48px">JOURNAL</a>
    <span class="abs" style="left:505px;top:61px;width:12px;height:1px;background:#fff"></span>
  </nav>
  <div class="btn" style="left:560px;top:39px;width:86px;height:26px">ENQUIRE</div>
  <div class="abs hero-title serif" style="left:0;top:176px;width:714px;font-size:22px">KATE AND TOM</div>
  <div class="abs hero-sub" style="left:0;top:209px;width:714px">Harrow Brook Inn Old Barn Wedding</div>
  <div class="abs hero-sub" style="left:280px;top:236px;width:160px;display:flex;align-items:center;gap:10px">
    <svg width="16" height="15" viewBox="0 0 16 15" fill="none" stroke="#fff" stroke-width="1"><rect x="1" y="2" width="14" height="12" rx="1"/><line x1="1" y1="5.5" x2="15" y2="5.5"/><line x1="5" y1="0.5" x2="5" y2="3.5"/><line x1="11" y1="0.5" x2="11" y2="3.5"/></svg>
    <span>12 August 2022 - Weddings</span>
  </div>

  <div class="abs photo warm" style="left:69px;top:407px;width:331px;height:228px" role="img" aria-label="Groom waiting as the bride walks down the aisle"></div>
  <div class="abs arrow light" style="left:337px;top:613px;width:31px;height:22px"><svg width="12" height="6"><path d="M12 3H1M4 0L1 3l3 3" stroke="#777" fill="none"/></svg></div>
  <div class="abs arrow" style="left:368px;top:613px;width:32px;height:22px"><svg width="12" height="6"><path d="M0 3h11M8 0l3 3-3 3" stroke="#333" fill="none"/></svg></div>
  <div class="abs serif" style="left:437px;top:449px;font-size:21px;color:var(--gold);font-weight:500">Tom and Kate's</div>
  <div class="abs serif" style="left:437px;top:482px;font-size:11.5px;font-weight:600">Harrow Brook Inn Old Barn Wedding</div>
  <p class="abs small" style="left:437px;top:508px;width:200px">Phasellus enim libero, blandit vel sapien vitae, condimentum ultricies magna et. Quisque euismod orci ut. Phasellus enim libero, blandit vel sapien vitae, condimentum ultricies magna et. Quisque euismod orci ut.</p>

  <div class="abs center" style="left:0;top:690px;width:714px;font-size:9px;color:var(--muted)">Highlights</div>
  <div class="abs h-gold" style="left:0;top:708px;width:714px;font-size:27px">HARROW BROOK INN</div>
  <div class="abs photo green" style="left:69px;top:754px;width:577px;height:235px" role="img" aria-label="Aerial film still of the inn and surrounding village at dusk"></div>
  <div class="abs" style="left:345px;top:858px;width:26px;height:26px;border-radius:50%;background:rgba(255,255,255,.55);display:flex;align-items:center;justify-content:center"><svg width="8" height="10"><path d="M0 0l8 5-8 5z" fill="#fff"/></svg></div>
  <div class="abs arrow light" style="left:57px;top:867px;width:26px;height:23px"><svg width="12" height="6"><path d="M12 3H1M4 0L1 3l3 3" stroke="#777" fill="none"/></svg></div>
  <div class="abs arrow" style="left:628px;top:867px;width:31px;height:23px"><svg width="12" height="6"><path d="M0 3h11M8 0l3 3-3 3" stroke="#333" fill="none"/></svg></div>
  <div class="abs photo green" style="left:175px;top:1006px;width:81px;height:57px" role="img" aria-label="Inn entrance with sign and greenery"></div>
  <div class="abs photo warm" style="left:270px;top:1006px;width:82px;height:57px" role="img" aria-label="Bridesmaids together"></div>
  <div class="abs photo suit" style="left:363px;top:1006px;width:81px;height:57px" role="img" aria-label="Wedding cake on a table"></div>
  <div class="abs photo blue" style="left:459px;top:1006px;width:81px;height:57px" role="img" aria-label="Glass roofed reception room"></div>
  <p class="abs small center" style="left:157px;top:1083px;width:400px">Phasellus enim libero, blandit vel sapien vitae, condimentum ultricies magna et. Quisque euismod orci ut. Phasellus enim libero, blandit vel sapien vitae, condimentum ultricies magna et. Quisque euismod orci ut. Phasellus enim libero, blandit vel sapien vitae, condimentum ultricies magna et.</p>

  <div class="abs band" style="left:0;top:1167px;width:714px;height:310px"></div>
  <div class="abs h-gold" style="left:0;top:1204px;width:714px;font-size:27px">SUPPLIERS</div>
  <div class="abs card" style="left:68px;top:1267px;width:184px;height:63px;padding-left:18px;gap:18px"><div class="sup-ico" style="width:34px;height:34px" role="img" aria-label="Venue illustration"></div><div><div class="lbl">Venue:</div><div class="val">Harrow Brook Inn</div></div></div>
  <div class="abs card" style="left:265px;top:1267px;width:184px;height:63px;padding-left:18px;gap:18px"><div class="sup-ico" style="width:34px;height:34px" role="img" aria-label="Photographer illustration"></div><div><div class="lbl">Photographer:</div><div class="val">RL Photo</div></div></div>
  <div class="abs card" style="left:462px;top:1267px;width:183px;height:63px;padding-left:18px;gap:18px"><div class="sup-ico" style="width:34px;height:34px" role="img" aria-label="Hair stylist illustration"></div><div><div class="lbl">Hair:</div><div class="val">Ivy Marsh</div></div></div>
  <div class="abs card" style="left:166px;top:1356px;width:183px;height:63px;padding-left:18px;gap:18px"><div class="sup-ico" style="width:34px;height:34px" role="img" aria-label="Make up artist illustration"></div><div><div class="lbl">Make Up:</div><div class="val">Tara Quinn</div></div></div>
  <div class="abs card" style="left:363px;top:1356px;width:183px;height:63px;padding-left:18px;gap:18px"><div class="sup-ico" style="width:34px;height:34px" role="img" aria-label="Florist bouquet illustration"></div><div><div class="lbl">Florist:</div><div class="val">Bloomfold</div></div></div>

  <div class="abs" style="left:68px;top:1508px;font-size:7px;color:var(--muted)">Previous Post</div>
  <div class="abs serif" style="left:68px;top:1521px;font-size:12.5px;font-weight:600">Wexley Hall Wedding In Northumberland</div>
  <div class="abs ico" style="left:475px;top:1521px;width:14px;height:14px"></div>
  <div class="abs ico" style="left:502px;top:1521px;width:14px;height:14px"></div>
  <div class="abs ico" style="left:527px;top:1522px;width:20px;height:13px"></div>
  <div class="abs" style="left:574px;top:1510px;width:72px;height:25px;background:#efefef;display:flex;align-items:center;gap:8px;padding-left:12px;font-size:7.5px">
    <svg width="11" height="11" fill="none" stroke="#555"><circle cx="9" cy="2" r="1.6"/><circle cx="2" cy="5.5" r="1.6"/><circle cx="9" cy="9" r="1.6"/><path d="M3.4 4.8 7.6 2.7M3.4 6.2l4.2 2.1"/></svg>10 Shares</div>
  <div class="abs" style="left:68px;top:1563px;width:578px;height:1px;background:var(--rule)"></div>

  <div class="abs h-gold" style="left:0;top:1594px;width:714px;font-size:27px">RELATED POSTS</div>

  <div class="abs photo" style="left:68px;top:1657px;width:283px;height:216px" role="img" aria-label="Groom kissing the bride's cheek"></div>
  <div class="abs datebox" style="left:75px;top:1663px;width:43px;height:45px"><div style="font-size:20px;line-height:26px;padding-top:4px">12</div><div style="font-size:6px">AUG</div></div>
  <div class="abs post-title" style="left:68px;top:1886px">Wexley Hall Wedding In Northumberland</div>
  <div class="abs" style="left:68px;top:1911px;font-size:6.5px;color:var(--muted)">Gorgeous wedding at the stunning and quirky Wexley Hall in Northumberland</div>
  <div class="abs read" style="left:69px;top:1934px">Read More</div>

  <div class="abs photo blue" style="left:363px;top:1657px;width:283px;height:216px" role="img" aria-label="Couple embracing under blue confetti by a vintage tractor"></div>
  <div class="abs datebox" style="left:369px;top:1663px;width:43px;height:45px"><div style="font-size:20px;line-height:26px;padding-top:4px">08</div><div style="font-size:6px">AUG</div></div>
  <div class="abs post-title" style="left:363px;top:1886px">The Romantic Wedding at the Red Lantern Ashby</div>
  <div class="abs" style="left:363px;top:1911px;font-size:6.5px;color:var(--muted)">The Romantic Wedding at the Red Lantern Ashby</div>
  <div class="abs read" style="left:364px;top:1934px">Read More</div>

  <div class="abs photo field" style="left:68px;top:1960px;width:283px;height:216px" role="img" aria-label="Aerial view of a couple lying in a golden field"></div>
  <div class="abs datebox" style="left:75px;top:1966px;width:43px;height:45px"><div style="font-size:20px;line-height:26px;padding-top:4px">12</div><div style="font-size:6px">AUG</div></div>
  <div class="abs post-title" style="left:68px;top:2190px">Wexley Hall Wedding In Northumberland</div>
  <div class="abs" style="left:68px;top:2215px;font-size:6.5px;color:var(--muted)">Gorgeous wedding at the stunning and quirky Wexley Hall in Northumberland</div>
  <div class="abs read" style="left:69px;top:2238px">Read More</div>

  <div class="abs photo suit" style="left:363px;top:1960px;width:283px;height:216px" role="img" aria-label="Bride laughing with the groom during the ceremony"></div>
  <div class="abs datebox" style="left:369px;top:1966px;width:43px;height:45px"><div style="font-size:20px;line-height:26px;padding-top:4px">08</div><div style="font-size:6px">AUG</div></div>
  <div class="abs post-title" style="left:363px;top:2190px">The Romantic Wedding at the Red Lantern Ashby</div>
  <div class="abs" style="left:363px;top:2215px;font-size:6.5px;color:var(--muted)">The Romantic Wedding at the Red Lantern Ashby</div>
  <div class="abs read" style="left:364px;top:2238px">Read More</div>

  <div class="btn" style="left:294px;top:2293px;width:126px;height:26px">LOAD MORE TESTIMONIALS</div>

  <div class="abs band" style="left:0;top:2351px;width:714px;height:279px"></div>
  <div class="abs serif center" style="left:0;top:2387px;width:714px;font-size:17px;letter-spacing:.28em;color:#7a6a45">FOLLOW ME ON INSTAGRAM</div>
  <div class="abs photo" style="left:68px;top:2437px;width:86px;height:96px" role="img" aria-label="Couple walking down a street"></div>
  <div class="abs photo warm" style="left:166px;top:2437px;width:86px;height:96px" role="img" aria-label="Couple posing under confetti"></div>
  <div class="abs photo green" style="left:264px;top:2437px;width:86px;height:96px" role="img" aria-label="Horse-drawn carriage in a field"></div>
  <div class="abs photo suit" style="left:362px;top:2437px;width:86px;height:96px" role="img" aria-label="Groom and groomsman in suits"></div>
  <div class="abs photo warm" style="left:460px;top:2437px;width:86px;height:96px" role="img" aria-label="Bride smiling at the groom"></div>
  <div class="abs photo blue" style="left:559px;top:2437px;width:86px;height:96px" role="img" aria-label="Wedding party jumping outdoors"></div>
  <div class="btn white" style="left:281px;top:2564px;width:152px;height:32px">Follow me @brunolesswayfilms</div>

  <div class="abs serif" style="left:68px;top:2700px;font-size:12px;letter-spacing:.2em;color:var(--gold);font-weight:600">BRUNO LESSWAY</div>
  <div class="abs ico" style="left:90px;top:2739px;width:14px;height:14px"></div>
  <div class="abs ico" style="left:116px;top:2739px;width:14px;height:14px"></div>
  <div class="abs ico" style="left:141px;top:2740px;width:18px;height:13px"></div>
  <div class="abs foot-h" style="left:245px;top:2676px">Contact</div>
  <svg class="abs" style="left:246px;top:2706px" width="10" height="10" fill="none" stroke="#999"><path d="M2 1l2 0 1 2.5-1.3 1a6 6 0 0 0 2.8 2.8l1-1.3L10 7v2c0 .6-.5 1-1 1A8 8 0 0 1 1 2c0-.6.4-1 1-1z"/></svg>
  <div class="abs foot-t" style="left:268px;top:2705px">07700 900 123</div>
  <svg class="abs" style="left:246px;top:2735px" width="10" height="8" fill="none" stroke="#999"><rect x=".5" y=".5" width="9" height="7"/><path d="M.5.5 5 4.5 9.5.5"/></svg>
  <div class="abs foot-t" style="left:268px;top:2733px">films@brunolessway.com</div>
  <div class="abs foot-h" style="left:416px;top:2676px">Links</div>
  <div class="abs foot-t" style="left:418px;top:2702px">FAQ's</div>
  <div class="abs foot-t" style="left:418px;top:2721px">Wedding Photography</div>
  <div class="abs foot-t" style="left:418px;top:2741px">Commercial</div>
  <div class="abs foot-t" style="left:546px;top:2702px">North East Wedding Venues</div>
  <div class="abs foot-t" style="left:546px;top:2721px">Free Speeches Guide</div>
  <div class="abs foot-t" style="left:546px;top:2741px">Blog</div>
  <div class="abs center" style="left:0;top:2782px;width:714px;font-size:6.5px;color:var(--muted)">© Copyright 2022 Bruno Lessway Films Ltd All Rights Reserved</div>
</section>

<!-- ================= MOBILE ================= -->
<section class="abs mobile">
  <div class="abs hero-shade" style="left:0;top:0;width:150px;height:230px" role="img" aria-label="Groom laughing under falling confetti"></div>
  <div class="abs brand" style="left:7px;top:26px;font-size:6.5px">BRUNO LESSWAY</div>
  <svg class="abs" style="left:129px;top:22px" width="12" height="8" stroke="#fff"><path d="M0 .5h12M3 4h9M0 7.5h12"/></svg>
  <div class="abs hero-title serif" style="left:0;top:108px;width:150px;font-size:16px">KATE AND TOM</div>
  <div class="abs hero-sub" style="left:0;top:135px;width:150px;font-size:6.5px">Harrow Brook Inn Old Barn Wedding</div>
  <div class="abs hero-sub" style="left:12px;top:158px;width:130px;font-size:6.5px;display:flex;gap:6px;align-items:center"><svg width="11" height="10" fill="none" stroke="#fff" stroke-width=".8"><rect x=".5" y="1.5" width="10" height="8"/><line x1=".5" y1="4" x2="10.5" y2="4"/></svg>12 August 2022 - Weddings</div>

  <div class="abs photo warm" style="left:2px;top:235px;width:145px;height:149px" role="img" aria-label="Groom and bride in the aisle"></div>
  <div class="abs arrow light" style="left:115px;top:372px;width:16px;height:12px"><svg width="7" height="4"><path d="M7 2H1M2.5 0 .5 2l2 2" stroke="#777" fill="none"/></svg></div>
  <div class="abs arrow" style="left:131px;top:372px;width:16px;height:12px"><svg width="7" height="4"><path d="M0 2h6M4.5 0l2 2-2 2" stroke="#333" fill="none"/></svg></div>
  <div class="abs serif" style="left:12px;top:401px;font-size:14px;color:var(--gold);font-weight:500">Tom and Kate's</div>
  <div class="abs serif" style="left:12px;top:426px;font-size:7.5px;font-weight:600">Harrow Brook Inn Old Barn Wedding</div>
  <p class="abs" style="left:12px;top:445px;width:128px;font-size:5.5px;line-height:12.3px;color:var(--muted)">Phasellus enim libero, blandit vel sapien vitae, condimentum ultricies magna et. Quisque euismod orci ut. Phasellus enim libero, blandit vel sapien vitae, condimentum ultricies magna et. Quisque euismod orci ut.</p>
  <div class="abs center" style="left:0;top:534px;width:150px;font-size:6.5px;color:var(--muted)">Highlights</div>
  <div class="abs h-gold" style="left:0;top:551px;width:150px;font-size:19px;line-height:24px">HARROW<br>BROOK INN</div>
  <div class="abs photo green" style="left:0;top:608px;width:150px;height:184px" role="img" aria-label="Aerial film still of the inn and village"></div>
  <div class="abs" style="left:64px;top:691px;width:22px;height:22px;border-radius:50%;background:rgba(255,255,255,.55);display:flex;align-items:center;justify-content:center"><svg width="6" height="8"><path d="M0 0l6 4-6 4z" fill="#fff"/></svg></div>
  <div class="abs arrow light" style="left:0;top:691px;width:22px;height:19px"><svg width="8" height="5"><path d="M8 2.5H1M3 .5l-2 2 2 2" stroke="#777" fill="none"/></svg></div>
  <div class="abs arrow" style="left:128px;top:691px;width:22px;height:19px"><svg width="8" height="5"><path d="M0 2.5h7M5 .5l2 2-2 2" stroke="#333" fill="none"/></svg></div>
  <div class="abs photo warm" style="left:4px;top:800px;width:65px;height:43px" role="img" aria-label="Bridesmaids together"></div>
  <div class="abs photo suit" style="left:79px;top:800px;width:64px;height:43px" role="img" aria-label="Wedding cake"></div>
  <div class="abs photo green" style="left:4px;top:851px;width:65px;height:44px" role="img" aria-label="Inn entrance"></div>
  <div class="abs photo blue" style="left:79px;top:851px;width:64px;height:44px" role="img" aria-label="Glass roofed reception room"></div>
  <p class="abs center" style="left:8px;top:905px;width:134px;font-size:5.5px;line-height:12.2px;color:var(--muted)">Phasellus enim libero, blandit vel sapien vitae, condimentum ultricies magna et. Quisque euismod orci ut. Phasellus enim libero, blandit vel sapien vitae, condimentum ultricies magna et. Quisque euismod orci ut. Phasellus enim libero, blandit vel sapien vitae, condimentum ultricies magna et.</p>

  <div class="abs band" style="left:0;top:999px;width:150px;height:341px"></div>
  <div class="abs h-gold" style="left:0;top:1016px;width:150px;font-size:19px">SUPPLIERS</div>
  <div class="abs card" style="left:2px;top:1048px;width:146px;height:49px;padding-left:12px;gap:14px"><div class="sup-ico" style="width:26px;height:26px" role="img" aria-label="Venue illustration"></div><div><div class="lbl" style="font-size:5px">Venue:</div><div class="val" style="font-size:7.5px">Harrow Brook Inn</div></div></div>
  <div class="abs card" style="left:2px;top:1104px;width:146px;height:49px;padding-left:12px;gap:14px"><div class="sup-ico" style="width:26px;height:26px" role="img" aria-label="Photographer illustration"></div><div><div class="lbl" style="font-size:5px">Photographer:</div><div class="val" style="font-size:7.5px">RL Photo</div></div></div>
  <div class="abs card" style="left:2px;top:1160px;width:146px;height:49px;padding-left:12px;gap:14px"><div class="sup-ico" style="width:26px;height:26px" role="img" aria-label="Hair stylist illustration"></div><div><div class="lbl" style="font-size:5px">Hair:</div><div class="val" style="font-size:7.5px">Ivy Marsh</div></div></div>
  <div class="abs card" style="left:2px;top:1215px;width:146px;height:49px;padding-left:12px;gap:14px"><div class="sup-ico" style="width:26px;height:26px" role="img" aria-label="Make up artist illustration"></div><div><div class="lbl" style="font-size:5px">Make Up:</div><div class="val" style="font-size:7.5px">Tara Quinn</div></div></div>
  <div class="abs card" style="left:2px;top:1270px;width:146px;height:49px;padding-left:12px;gap:14px"><div class="sup-ico" style="width:26px;height:26px" role="img" aria-label="Florist bouquet illustration"></div><div><div class="lbl" style="font-size:5px">Florist:</div><div class="val" style="font-size:7.5px">Bloomfold</div></div></div>

  <div class="abs" style="left:7px;top:1354px;font-size:5px;color:var(--muted)">Previous Post</div>
  <div class="abs serif" style="left:7px;top:1365px;width:130px;font-size:9px;line-height:14px;font-weight:600">Wexley Hall Wedding In Northumberland</div>
  <div class="abs ico" style="left:9px;top:1403px;width:10px;height:10px"></div>
  <div class="abs ico" style="left:28px;top:1403px;width:10px;height:10px"></div>
  <div class="abs ico" style="left:47px;top:1404px;width:13px;height:9px"></div>
  <div class="abs" style="left:7px;top:1430px;width:57px;height:19px;background:#efefef;font-size:5.5px;display:flex;align-items:center;gap:6px;padding-left:8px"><svg width="8" height="8" fill="none" stroke="#555" stroke-width=".8"><circle cx="6.5" cy="1.5" r="1.2"/><circle cx="1.5" cy="4" r="1.2"/><circle cx="6.5" cy="6.5" r="1.2"/></svg>10 Shares</div>
  <div class="abs" style="left:7px;top:1463px;width:136px;height:1px;background:var(--rule)"></div>
  <div class="abs h-gold" style="left:0;top:1482px;width:150px;font-size:19px;line-height:25px">RELATED<br>POSTS</div>

  <div class="abs photo" style="left:0;top:1545px;width:150px;height:169px" role="img" aria-label="Groom kissing the bride's cheek"></div>
  <div class="abs datebox" style="left:6px;top:1550px;width:33px;height:33px"><div style="font-size:14px;line-height:18px;padding-top:3px">12</div><div style="font-size:4.5px">AUG</div></div>
  <div class="abs post-title" style="left:7px;top:1724px;width:130px;font-size:9px;line-height:14px">Wexley Hall Wedding In Northumberland</div>
  <div class="abs" style="left:7px;top:1757px;width:135px;font-size:4.5px;line-height:10px;color:var(--muted)">Gorgeous wedding at the stunning and quirky Wexley Hall in Northumberland</div>
  <div class="abs read" style="left:8px;top:1784px;font-size:5px">Read More</div>

  <div class="abs photo blue" style="left:0;top:1810px;width:150px;height:170px" role="img" aria-label="Couple embracing under blue confetti"></div>
  <div class="abs datebox" style="left:6px;top:1815px;width:33px;height:33px"><div style="font-size:14px;line-height:18px;padding-top:3px">08</div><div style="font-size:4.5px">AUG</div></div>
  <div class="abs post-title" style="left:4px;top:1989px;width:140px;font-size:9px;line-height:14px">The Romantic Wedding at the Red Lantern Ashby</div>
  <div class="abs" style="left:4px;top:2021px;font-size:4.5px;color:var(--muted)">The Romantic Wedding at the Red Lantern Ashby</div>
  <div class="abs read" style="left:4px;top:2036px;font-size:5px">Read More</div>
  <div class="btn" style="left:24px;top:2072px;width:99px;height:19px;font-size:5.5px">LOAD MORE TESTIMONIALS</div>

  <div class="abs band" style="left:0;top:2113px;width:150px;height:345px"></div>
  <div class="abs serif center" style="left:0;top:2134px;width:150px;font-size:10px;line-height:17px;letter-spacing:.22em;color:#7a6a45">FOLLOW ME ON<br>INSTAGRAM</div>
  <div class="abs photo" style="left:3px;top:2180px;width:69px;height:70px" role="img" aria-label="Couple on a street"></div>
  <div class="abs photo warm" style="left:75px;top:2180px;width:69px;height:70px" role="img" aria-label="Couple under confetti"></div>
  <div class="abs photo green" style="left:3px;top:2255px;width:69px;height:70px" role="img" aria-label="Horse-drawn carriage"></div>
  <div class="abs photo suit" style="left:75px;top:2255px;width:69px;height:70px" role="img" aria-label="Groom and groomsman"></div>
  <div class="abs photo warm" style="left:3px;top:2330px;width:69px;height:70px" role="img" aria-label="Bride smiling at the groom"></div>
  <div class="abs photo blue" style="left:75px;top:2330px;width:69px;height:70px" role="img" aria-label="Wedding party jumping"></div>
  <div class="btn white" style="left:18px;top:2416px;width:118px;height:24px;font-size:6px">Follow me @brunolesswayfilms</div>

  <div class="abs serif center" style="left:0;top:2500px;width:150px;font-size:9px;letter-spacing:.18em;color:var(--gold);font-weight:600">BRUNO LESSWAY</div>
  <div class="abs ico" style="left:51px;top:2529px;width:11px;height:11px"></div>
  <div class="abs ico" style="left:71px;top:2529px;width:11px;height:11px"></div>
  <div class="abs ico" style="left:90px;top:2530px;width:14px;height:10px"></div>
  <div class="abs foot-h" style="left:19px;top:2570px;font-size:7px">Contact</div>
  <div class="abs foot-t" style="left:36px;top:2593px;font-size:5.5px">07700 900 123</div>
  <div class="abs foot-t" style="left:36px;top:2615px;font-size:5.5px">films@brunolessway.com</div>
  <svg class="abs" style="left:19px;top:2593px" width="8" height="8" fill="none" stroke="#999"><path d="M1.5.8h1.5l.8 2-1 .8a4.8 4.8 0 0 0 2.2 2.2l.8-1 2 .8v1.5c0 .5-.4.8-.8.8A6.5 6.5 0 0 1 .8 1.6c0-.5.3-.8.7-.8z"/></svg>
  <svg class="abs" style="left:19px;top:2616px" width="8" height="6" fill="none" stroke="#999"><rect x=".5" y=".5" width="7" height="5"/><path d="M.5.5 4 3.5 7.5.5"/></svg>
  <div class="abs foot-h" style="left:19px;top:2641px;font-size:7px">Links</div>
  <div class="abs foot-t" style="left:20px;top:2661px;font-size:5px">FAQ's</div>
  <div class="abs foot-t" style="left:20px;top:2677px;font-size:5px">Wedding Photography</div>
  <div class="abs foot-t" style="left:20px;top:2694px;font-size:5px">Commercial</div>
  <div class="abs foot-t" style="left:20px;top:2710px;font-size:5px">North East Wedding Venues</div>
  <div class="abs foot-t" style="left:20px;top:2726px;font-size:5px">Free Speeches Guide</div>
  <div class="abs foot-t" style="left:20px;top:2743px;font-size:5px">Blog</div>
  <div class="abs" style="left:20px;top:2768px;width:120px;font-size:4.5px;line-height:11px;color:var(--muted)">© Copyright 2022 Bruno Lessway Films Ltd.<br>All Rights Reserved</div>
</section>

</body>
</html>
```